Quorva - corporate Business Card

We need a good look and innovative business card for a new start up company based in Los Angeles called "Quorva". We are in a payment business, including payment card, app, and ewallet. We are expert in online payment and Card not present (CNP) transaction.
We need an innovative, modern business card.

Our logo font is Aero Matics

Target Market(s)

Startup - Bank - Online Payment - Card Manufacturing

Industry/Entity Type

Startup

Contact Information for Business Card

phone: 555 014 7396 - Address: 4172 Marlowe blvd, Harwick Falls, NV 90299

Requirements
Must have
• Message: innovative, professional, expert, high tech, trust, online payment expert, security
Nice to have
• no comment
Should not have
• no Comment

```html
<!DOCTYPE html>
<html lang="en">
<head>
<meta charset="utf-8">
<title>Quorva – Business Card</title>
<link rel="stylesheet" href="https://fonts.googleapis.com/css2?family=Lato:wght@400;700;900&display=swap">
<style>
  :root {
    --backdrop: #acacac;
    --brand-red: #b71e2d;
    --blush: #f2dcdf;
    --card-light: #e6e6e6;
    --ink-grey: #5f5f5f;
  }
  html, body {
    margin: 0;
    padding: 0;
    width: 1200px;
    height: 900px;
    overflow: hidden;
    background: var(--backdrop);
    font-family: "Lato", Arial, sans-serif;
  }
  .canvas {
    position: relative;
    width: 1200px;
    height: 900px;
  }
  .card {
    position: absolute;
    top: 215px;
    width: 414px;
    height: 414px;
    border-radius: 50%;
    box-sizing: border-box;
  }
  .card-front {
    left: 164px;
    background: var(--brand-red);
    display: flex;
    align-items: center;
    justify-content: center;
  }
  .front-disc {
    width: 280px;
    height: 280px;
    border-radius: 50%;
    background: var(--blush);
    display: flex;
    align-items: center;
    justify-content: center;
  }
  .front-wordmark {
    color: var(--brand-red);
    font-weight: 700;
    font-size: 56px;
    letter-spacing: 1px;
    line-height: 1;
  }
  .card-back {
    left: 623px;
    background: var(--card-light);
    text-align: center;
  }
  .holder-name {
    position: absolute;
    top: 70px;
    left: 0;
    right: 0;
    color: var(--brand-red);
    font-weight: 900;
    font-size: 20px;
    letter-spacing: 0.5px;
    text-transform: uppercase;
  }
  .holder-role {
    position: absolute;
    top: 93px;
    left: 0;
    right: 0;
    color: var(--ink-grey);
    font-size: 18px;
  }
  .brand-lockup {
    position: absolute;
    top: 148px;
    left: 46px;
    display: flex;
    align-items: center;
    gap: 14px;
  }
  .brand-dot {
    width: 96px;
    height: 96px;
    border-radius: 50%;
    background: var(--brand-red);
  }
  .brand-name {
    color: var(--brand-red);
    font-weight: 700;
    font-size: 62px;
    line-height: 1;
    letter-spacing: 1px;
  }
  .contact-phone {
    position: absolute;
    top: 277px;
    left: 0;
    right: 0;
    color: var(--ink-grey);
    font-size: 19px;
    display: flex;
    justify-content: center;
    align-items: center;
    gap: 6px;
  }
  .contact-phone svg { width: 15px; height: 15px; fill: var(--brand-red); }
  .contact-address {
    position: absolute;
    top: 313px;
    left: 0;
    right: 0;
    color: var(--ink-grey);
    font-size: 19px;
    line-height: 24px;
    font-style: normal;
  }
</style>
</head>
<body>
<main class="canvas">
  <section class="card card-front" aria-label="Card front">
    <div class="front-disc">
      <span class="front-wordmark">Quorva</span>
    </div>
  </section>

  <section class="card card-back" aria-label="Card back">
    <div class="holder-name">Marcellus Harlow</div>
    <div class="holder-role">Managing Director</div>
    <div class="brand-lockup">
      <span class="brand-dot"></span>
      <span class="brand-name">Quorva</span>
    </div>
    <div class="contact-phone">
      <svg viewBox="0 0 24 24" aria-hidden="true"><path d="M6.6 10.8c1.4 2.8 3.8 5.1 6.6 6.6l2.2-2.2c.3-.3.7-.4 1-.2 1.1.4 2.3.6 3.6.6.6 0 1 .4 1 1V20c0 .6-.4 1-1 1C10.6 21 3 13.4 3 4c0-.6.4-1 1-1h3.5c.6 0 1 .4 1 1 0 1.3.2 2.5.6 3.6.1.3 0 .7-.2 1L6.6 10.8z"/></svg>
      <span>555 014 7396</span>
    </div>
    <address class="contact-address">4172 Marlowe blvd,<br>Harwick Falls, NV 90299</address>
  </section>
</main>
</body>
</html>
```